Corvana Tongue Works, LLC

We need a business card that includes information about our business and conveys a reliable business that provides document translation services and interpreters for a variety of corporate and individual clients. We want to come across as professional, reliable, yet approachable. It should include the following on one side:

ESL / ENL Language Classes, Private Lessons, and Online Tutors
PLEXA Training and Testing
Translating & Interpreting Services
Contact us about Over-the-Phone Interpreting in over 200 languages
24/7/365
www.corvanatongue.example

The other side should include (555) 481-3062

Rhoda Pelling, President
482 Garnet Ave., Ste. 219
Indianapolis, IN 40917

Please add USA as part of the address. Also, please add rmpelling@corvanatongueworks.example as the e-mail address. Thank you.

Target Market(s)

Business professionals, their families, the international community

Industry/Entity Type

Business

Contact Information for Business Card

24/7/365
www.corvanatongue.example

(555) 481-3062

Rhoda Pelling, President
482 Garnet Ave., Ste. 219
Indianapolis, IN 40917
USA

Font styles to use
Sans Serif

Colors

Designer to choose colors to be used in the design.

Requirements
Must have
• See project description
• e-mail address and web address
• Phone number
Nice to have
• a globe
• physical address
Should not have
• Should not have the same color scheme as other agencies in our market in Indiana unless it is blue and black. No purple or yellow.

```html
<!DOCTYPE html>
<html lang="en">
<head>
<meta charset="utf-8">
<title>Corvana Tongue Works – Business Card</title>
<link href="https://fonts.googleapis.com/css2?family=Source+Sans+3:wght@400;600&family=Source+Serif+4:wght@400&display=swap" rel="stylesheet">
<style>
  :root {
    --bg: #d8d8d8;
    --card: #ffffff;
    --blue: #4a90c4;
    --blue-text: #3f86c4;
    --ink: #1a1a1a;
  }
  * { margin: 0; padding: 0; box-sizing: border-box; }
  html, body { width: 1200px; height: 800px; overflow: hidden; }
  body {
    background: var(--bg);
    position: relative;
    font-family: "Source Sans 3", "Myriad Pro", Arial, sans-serif;
  }
  .card {
    position: absolute;
    top: 281px;
    width: 432px;
    height: 244px;
    background: var(--card);
  }
  .card--front { left: 109px; }
  .card--back { left: 638px; }

  /* Front */
  .holder { position: absolute; top: 46px; left: 0; width: 100%; text-align: center; color: var(--blue-text); }
  .holder__name { font-size: 22px; font-weight: 400; line-height: 1; }
  .holder__title { font-size: 12px; margin-top: 3px; }
  .contact-band {
    position: absolute; top: 97px; left: 0; width: 100%; height: 82px;
    background: var(--blue); color: #fff;
  }
  .contact-item { position: absolute; text-align: center; font-size: 7.5px; line-height: 1.3; }
  .contact-item svg { display: block; margin: 0 auto 4px; }
  .contact-item--address { left: 30px; width: 170px; top: 21px; }
  .contact-item--email { left: 230px; width: 170px; top: 30px; }
  .contact-item--phone { left: 150px; width: 132px; top: 190px; color: var(--blue-text); }

  /* Back */
  .globe-note { position: absolute; left: 52px; top: 78px; width: 110px; text-align: center; color: var(--blue-text);
    font-family: "Source Serif 4", Georgia, serif; font-size: 6.4px; line-height: 1.25; }
  .globe-note svg { display: block; margin: 0 auto 3px; }
  .divider { position: absolute; left: 172px; top: 41px; width: 1px; height: 158px; background: var(--ink); }
  .brand { position: absolute; left: 182px; top: 54px; display: flex; align-items: center; gap: 5px; }
  .brand__dot { width: 40px; height: 40px; border-radius: 50%; background: var(--blue); }
  .brand__name { color: var(--blue-text); font-size: 12px; font-weight: 600; line-height: 1.05; }
  .services { position: absolute; left: 182px; top: 103px; color: var(--blue-text); font-size: 12.4px; line-height: 1.25; }
  .services li { list-style: none; }
  .services li + li { margin-top: 9px; }
  .website { position: absolute; left: 96px; top: 202px; width: 120px; text-align: center; font-size: 7px; font-weight: 600; color: var(--ink); }
</style>
</head>
<body>
  <section class="card card--front" aria-label="Card front">
    <div class="holder">
      <h1 class="holder__name">Rhoda Pelling</h1>
      <p class="holder__title">President</p>
    </div>
    <div class="contact-band">
      <div class="contact-item contact-item--address">
        <svg width="14" height="18" viewBox="0 0 14 18" aria-hidden="true">
          <path d="M7 0C3.1 0 0 3 0 6.8 0 11.5 7 18 7 18s7-6.5 7-11.2C14 3 10.9 0 7 0z" fill="#fff"/>
          <circle cx="7" cy="6.8" r="2.6" fill="var(--blue)"/>
        </svg>
        482 Garnet Ave., Ste. 219 Indianapolis, IN 40917<br>USA
      </div>
      <div class="contact-item contact-item--email">
        <svg width="20" height="13" viewBox="0 0 20 13" aria-hidden="true">
          <rect x="0.5" y="0.5" width="19" height="12" fill="#fff"/>
          <path d="M0.5 0.5 10 7.5 19.5 0.5M0.5 12.5 7.5 6M19.5 12.5 12.5 6" stroke="var(--blue)" stroke-width="1.2" fill="none"/>
        </svg>
        rmpelling@corvanatongueworks.example
      </div>
    </div>
    <div class="contact-item contact-item--phone">
      <svg width="16" height="16" viewBox="0 0 24 24" aria-hidden="true">
        <path d="M6.6 10.8c1.4 2.8 3.8 5.1 6.6 6.6l2.2-2.2c.3-.3.7-.4 1-.2 1.1.4 2.3.6 3.6.6.6 0 1 .4 1 1V20c0 .6-.4 1-1 1C10.6 21 3 13.4 3 4c0-.6.4-1 1-1h3.5c.6 0 1 .4 1 1 0 1.3.2 2.5.6 3.6.1.3 0 .7-.2 1z" fill="var(--blue)"/>
      </svg>
      (555) 481-3062
    </div>
  </section>

  <section class="card card--back" aria-label="Card back">
    <div class="globe-note">
      <svg width="36" height="36" viewBox="0 0 36 36" aria-hidden="true">
        <g fill="none" stroke="var(--blue)" stroke-width="1.3">
          <circle cx="18" cy="18" r="16.5"/>
          <ellipse cx="18" cy="18" rx="7.5" ry="16.5"/>
          <line x1="18" y1="1.5" x2="18" y2="34.5"/>
          <line x1="1.5" y1="18" x2="34.5" y2="18"/>
          <path d="M4 9.5h28M4 26.5h28"/>
        </g>
      </svg>
      Contact us about Over-the-Phone Interpreting in over 200 languages<br>24/7/365
    </div>
    <div class="divider"></div>
    <div class="brand">
      <span class="brand__dot" aria-hidden="true"></span>
      <span class="brand__name">Corvana<br>Tongue<br>Works, LLC</span>
    </div>
    <ul class="services">
      <li>ESL / ENL Language Classes,<br>Private Lessons, and Online Tutors</li>
      <li>PLEXA Training and Testing</li>
      <li>Translating &amp; Interpreting Services</li>
    </ul>
    <p class="website">www.corvanatongue.example</p>
  </section>
</body>
</html>
```